Business cards for a fun web development agency

Hi,I am building a web development agency. You can read about it on the website http://kite-loft.examplehost.com. Basically, I want to focus on free and open source products and stay as far away from the corporate business feeling as possible. I want to build a community so I want the business card to feel fun and approachable (at the risk of professional if need be). I am uploading some of my image assets in various file formats. Feel free to use them or make your own if you want just keeping in theme with the website.
Industry/Entity Type
Building
Contact Information for Business Card
Company Name: Boat ShedWebsite: www.kiteloftdev.example (it's currently in alpha on http://kite-loft.examplehost.com if you want to see the them we are trying to capture)My name is: Banner B. SchaferMy email: banner@boatsheddev.comMy phone: 0431 587 904
Look and feel

```html
<!DOCTYPE html>
<html lang="en">
<head>
<meta charset="utf-8">
<title>Kite Loft — Business Cards</title>
<link rel="stylesheet" href="https://fonts.googleapis.com/css2?family=Arimo:wght@400;700&display=swap">
<style>
  :root {
    --bg: #ecebe8;
    --teal-deep: #0f7fa6;
    --teal: #1fa8c9;
    --teal-light: #38bcd6;
    --paper: #f7f7f6;
    --paper-shade: #e6e6e4;
    --ink: #4a74a8;
    --ink-soft: #7d94b3;
    --rule: #b9c6d6;
    --white: #ffffff;
  }
  * { box-sizing: border-box; margin: 0; padding: 0; }
  html, body { width: 1200px; height: 902px; overflow: hidden; }
  body {
    background: var(--bg);
    font-family: "Arimo", Arial, sans-serif;
    position: relative;
  }
  .card {
    position: absolute;
    width: 560px;
    height: 320px;
    overflow: hidden;
    background: linear-gradient(135deg, var(--white) 0%, var(--paper) 60%, var(--paper-shade) 100%);
    box-shadow: 0 14px 30px rgba(0,0,0,.22);
  }

  /* ---------- Front ---------- */
  .card--front { left: 110px; top: 80px; }
  .card--front .panel-blue {
    position: absolute; left: 0; top: 0; bottom: 0; width: 330px;
    background: linear-gradient(160deg, var(--teal-deep) 0%, var(--teal) 45%, var(--teal-light) 100%);
  }
  .card--front .notch {
    position: absolute; right: 0; top: 58px;
    width: 0; height: 0;
    border-top: 32px solid transparent;
    border-bottom: 32px solid transparent;
    border-right: 62px solid var(--teal);
  }
  .band-rule {
    position: absolute; left: 70px; width: 260px; height: 1px;
    background: rgba(255,255,255,.75);
  }
  .band-rule--top { top: 118px; }
  .band-rule--bottom { top: 204px; }
  .front-brand {
    position: absolute; left: 40px; top: 140px; width: 290px;
    display: flex; align-items: center; justify-content: center; gap: 12px;
    color: var(--white); font-size: 38px; font-weight: 400; letter-spacing: 1px;
  }
  .brand-dot {
    width: 30px; height: 30px; border-radius: 50%; background: var(--white);
    flex: none;
  }

  /* ---------- Back ---------- */
  .card--back { left: 530px; top: 500px; }
  .card--back .panel-blue {
    position: absolute; left: 0; top: 0; bottom: 0; width: 250px;
    background: linear-gradient(160deg, var(--teal-deep) 0%, var(--teal) 50%, var(--teal-light) 100%);
  }
  .card--back .notch {
    position: absolute; left: 0; top: 40px;
    width: 0; height: 0;
    border-top: 36px solid transparent;
    border-bottom: 36px solid transparent;
    border-left: 70px solid var(--paper);
  }
  .mark-tile {
    position: absolute; left: 110px; top: 200px; width: 96px; height: 96px;
    background: var(--white);
  }
  .back-brand {
    position: absolute; left: 272px; top: 28px;
    display: flex; align-items: center; gap: 10px;
    color: var(--ink); font-size: 36px; font-weight: 400; letter-spacing: 1px;
  }
  .back-brand .brand-dot { background: var(--teal); width: 28px; height: 28px; }
  .holder-name {
    position: absolute; left: 272px; top: 104px;
    padding-left: 12px; border-left: 2px solid var(--teal);
    color: var(--ink); font-size: 24px; font-weight: 700; line-height: 30px;
  }
  .rule {
    position: absolute; left: 250px; right: 0; height: 1px; background: var(--rule);
  }
  .rule--1 { top: 100px; }
  .rule--2 { top: 144px; }
  .rule--3 { top: 180px; }
  .rule--4 { top: 216px; }
  .rule--5 { top: 252px; }
  .contact {
    position: absolute; left: 286px;
    color: var(--ink-soft); font-size: 15px; line-height: 20px;
  }
  .contact--phone { top: 152px; }
  .contact--web { top: 188px; }
  .contact--mail { top: 224px; }
  .icon {
    position: absolute; left: 222px; width: 26px; height: 26px; border-radius: 50%;
    border: 1.5px solid var(--white);
    display: flex; align-items: center; justify-content: center;
  }
  .icon svg { width: 13px; height: 13px; }
  .icon--phone { top: 149px; }
  .icon--web { top: 185px; }
  .icon--mail { top: 221px; }
</style>
</head>
<body>

  <section class="card card--front" aria-label="Business card front">
    <div class="panel-blue"></div>
    <div class="notch"></div>
    <div class="band-rule band-rule--top"></div>
    <div class="band-rule band-rule--bottom"></div>
    <div class="front-brand"><span>KITE</span><span class="brand-dot"></span><span>LOFT</span></div>
  </section>

  <section class="card card--back" aria-label="Business card back">
    <div class="panel-blue"></div>
    <div class="notch"></div>
    <div class="mark-tile"></div>

    <div class="back-brand"><span>KITE</span><span class="brand-dot"></span><span>LOFT</span></div>

    <div class="rule rule--1"></div>
    <div class="holder-name">Corwin T. Aldous</div>
    <div class="rule rule--2"></div>
    <div class="rule rule--3"></div>
    <div class="rule rule--4"></div>
    <div class="rule rule--5"></div>

    <span class="icon icon--phone">
      <svg viewBox="0 0 24 24" fill="none" stroke="#fff" stroke-width="2.4" stroke-linecap="round" stroke-linejoin="round"><path d="M5 3h4l2 5-3 2a12 12 0 0 0 6 6l2-3 5 2v4a2 2 0 0 1-2 2A18 18 0 0 1 3 5a2 2 0 0 1 2-2z"/></svg>
    </span>
    <span class="icon icon--web">
      <svg viewBox="0 0 24 24" fill="none" stroke="#fff" stroke-width="2.4" stroke-linecap="round" stroke-linejoin="round"><rect x="2" y="3" width="20" height="14" rx="1"/><path d="M8 21h8M12 17v4"/></svg>
    </span>
    <span class="icon icon--mail">
      <svg viewBox="0 0 24 24" fill="none" stroke="#fff" stroke-width="2.4" stroke-linejoin="round"><rect x="2" y="5" width="20" height="14"/><path d="M2 5l10 8 10-8"/></svg>
    </span>

    <div class="contact contact--phone">0431 587 904</div>
    <div class="contact contact--web">www.kiteloftdev.example</div>
    <div class="contact contact--mail">corwin@kiteloftdev.example</div>
  </section>

</body>
</html>
```